interior designer/stylist looking for a letter press business card to reflect the stylish work

Hello Designers,
I need a business card design for an company called Mosaic Interior Design. I'm aiming at the high end residential and private client market in London providing sleek simple interiors. I'd like my business card to be pinterest worthy and expensive looking, i want people to pin it and for it to have a sought after look, and want prospective customers to hire me as their interior designer as my card is so beautiful.
I love letter press design. I also like the use of colour/foil on the edge.
Colour combos & general things I like -
Black and White
Navy Blue and Gold
Neutral colours (muted palette of greys whites navys beiges)
White Marble & brass
Vorelle (fashion designer)
....also open to other suggestions....
Please dont take the pink in the attached photos too literally. i'd like the card to look more masculine than feminine.
I'd like Mosaic on one side in one font, with interior design underneath so one word will make the statement....... unless anyone has any other ideas, open to suggestions.
I'd like a really simple font and for the whole card to look very graphic.
my details -
Petra Wendlecombe
Interior Designer & Stylist
email petra@mosaicinteriordesign.co.uk
phone +447311584209
website wwww.mosaicinteriordesign.co.uk
GO GO GO!! EXCITED TO SEE THE OUTCOME!!
x P
Target Market(s)
High End Residential and private clients
Industry/Entity Type
Business
Contact Information for Business Card
Mosaic Interior Design & Styling
Petra Wendlecombe
phone +447311584209

```html
<!DOCTYPE html>
<html lang="en">
<head>
<meta charset="utf-8">
<title>Mosaic Interior Design — Business Card</title>
<link href="https://fonts.googleapis.com/css2?family=Jost:wght@300;400&display=swap" rel="stylesheet">
<style>
  :root {
    --backdrop: #ececec;
    --card-stock: #ffffff;
    --edge-paint: #4a4a4a;
    --ink: #6a6a6a;
    --ink-soft: #8a8a8a;
  }
  html, body {
    margin: 0;
    padding: 0;
    width: 1200px;
    height: 716px;
    overflow: hidden;
    background: var(--backdrop);
  }
  .stage {
    position: relative;
    width: 1200px;
    height: 716px;
    display: flex;
    align-items: center;
    justify-content: center;
    gap: 60px;
    font-family: "Jost", "Futura", sans-serif;
    color: var(--ink);
  }
  .card {
    box-sizing: border-box;
    width: 500px;
    height: 286px;
    background: var(--card-stock);
    border: 4px solid var(--edge-paint);
    box-shadow: 0 6px 18px rgba(0, 0, 0, 0.12);
    position: relative;
  }

  /* Back: contact side */
  .card--contact {
    padding: 58px 0 0 64px;
  }
  .contact__name {
    margin: 0;
    font-weight: 300;
    font-size: 30px;
    letter-spacing: 0.06em;
    text-transform: uppercase;
    line-height: 1;
  }
  .contact__role {
    margin: 10px 0 0;
    font-weight: 300;
    font-size: 10px;
    letter-spacing: 0.42em;
    text-transform: uppercase;
    color: var(--ink-soft);
  }
  .contact__details {
    list-style: none;
    margin: 34px 0 0;
    padding: 0;
    font-weight: 300;
    font-size: 11.5px;
    letter-spacing: 0.05em;
    text-transform: uppercase;
    line-height: 1.9;
  }

  /* Front: brand side */
  .card--brand {
    display: flex;
    flex-direction: column;
    align-items: center;
    justify-content: center;
  }
  .brand__name {
    margin: 0;
    font-weight: 300;
    font-size: 78px;
    letter-spacing: 0.08em;
    text-transform: uppercase;
    line-height: 1;
    padding-left: 0.08em;
  }
  .brand__descriptor {
    margin: 8px 0 0;
    font-weight: 300;
    font-size: 14px;
    letter-spacing: 0.38em;
    text-transform: uppercase;
    padding-left: 0.38em;
  }
</style>
</head>
<body>
  <main class="stage">
    <section class="card card--contact" aria-label="Contact side">
      <h2 class="contact__name">Petra Wendlecombe</h2>
      <p class="contact__role">Interior Designer &amp; Stylist</p>
      <ul class="contact__details">
        <li>petra@mosaicinteriordesign.co.uk</li>
        <li>+447311584209</li>
        <li>www.mosaicinteriordesign.co.uk</li>
      </ul>
    </section>

    <section class="card card--brand" aria-label="Brand side">
      <h1 class="brand__name">Mosaic</h1>
      <p class="brand__descriptor">Interior Design</p>
    </section>
  </main>
</body>
</html>
```